Pediatric Therapy Clinic Brochure

We need a Brochure for a new pediatric therapy clinic. The clinic offers occupational therapy, physical therapy, speech therapy and feeding therapy. We want a brochure for parents, doctors and medical professional. It should have a fun and inviting, but still professional feel. Should be kid focused, bright and colorful. All the text / wording is there and a rough layout. Now I need someone to tidy and jazz it up and make it look professional.

Target Market(s)

Parents, doctors, medical professional

Industry/Entity Type

Medical

Font styles to use
Serif
Sans Serif

Requirements
Must have
• Keep All the text with information about services the same. Logo on front. Pictures throughout (use any of the pictures provided) (try and match up with corresponding service) (pictures are labeled). Need to have Map and contact info
• Keep colors consistent with our logo
Nice to have
• Background, special effects. Make it look fancy and professional
Should not have
• Not so busy that is takes away from the text

```html
<!DOCTYPE html>
<html lang="en">
<head>
<meta charset="utf-8">
<title>Brightbrook Pediatric Therapy – Brochure Inside</title>
<link href="https://fonts.googleapis.com/css2?family=Oswald:wght@600;700&family=Arimo:wght@400;700&display=swap" rel="stylesheet">
<style>
  :root{
    --stage:#8c8c8e;
    --paper:#e6eff1;
    --paper-edge:#d6e2e5;
    --navy:#1d4f9e;
    --orange:#e6621b;
    --lime:#b6d433;
    --ink:#23406f;
    --photo-warm:#e9c7a6;
    --photo-cool:#c9d6e4;
  }
  *{box-sizing:border-box;margin:0;padding:0}
  html,body{width:1200px;height:1200px;overflow:hidden}
  body{background:var(--stage);display:flex;align-items:center;justify-content:center;font-family:"Arimo",Arial,sans-serif}
  .brochure{position:relative;width:1140px;height:800px;display:grid;grid-template-columns:repeat(3,1fr);background:var(--paper);box-shadow:0 14px 40px rgba(0,0,0,.3);overflow:hidden}
  .panel{position:relative;padding:26px 28px;border-right:1px solid var(--paper-edge);display:flex;flex-direction:column}
  .panel:last-child{border-right:none}
  .swoosh{position:absolute;pointer-events:none}
  .photo{border-radius:4px}
  .photo--hero{height:230px;margin:-26px -28px 14px;border-radius:0 0 0 0;background:linear-gradient(135deg,#f3f1ee,var(--photo-warm) 55%,#d96b5a)}
  .photo-pair{display:grid;grid-template-columns:1fr 1fr;gap:12px;margin-top:auto;position:relative;z-index:1}
  .photo--small{height:150px;border:5px solid #fff}
  .photo--bowl{background:linear-gradient(160deg,#f6eee4,#e4a066 60%,#c9552e)}
  .photo--ball{background:linear-gradient(160deg,#f4f4f4,#d44a3c 55%,#2b53b8)}
  .service{text-align:center;margin-bottom:12px}
  .service__title{font-family:"Oswald",Impact,sans-serif;font-weight:700;font-size:28px;color:var(--navy);text-transform:uppercase;line-height:1.05;letter-spacing:.2px}
  .service__lead{font-size:13px;color:var(--ink);margin-top:4px;line-height:1.3}
  .service__rule{height:3px;background:var(--navy);border-radius:2px;margin:8px 0 8px}
  .service__list{list-style:none;text-align:left}
  .service__list li{font-weight:700;color:var(--orange);font-size:14px;line-height:1.32;padding-left:14px;position:relative}
  .service__list li::before{content:"•";position:absolute;left:0}
  .brand{margin-top:auto;text-align:center;display:flex;align-items:center;justify-content:center;gap:10px;padding-bottom:10px}
  .brand__mark{width:22px;height:22px;border-radius:50%;background:var(--orange)}
  .brand__name{font-family:"Arimo",Arial,sans-serif;font-weight:700;font-size:24px;color:var(--navy);line-height:1.1}
  .note{position:relative;z-index:1;margin-top:auto;text-align:right;color:var(--orange);font-size:14px;padding-bottom:4px}
</style>
</head>
<body>
<main class="brochure">

  <section class="panel panel--occupational">
    <div class="photo photo--hero" role="img" aria-label="Smiling boy showing hands covered in bright finger paint"></div>
    <div class="service">
      <h2 class="service__title">Occupational Therapy</h2>
      <p class="service__lead">Helping children build better self-esteem, confidence and independence in all the things they do.</p>
      <div class="service__rule"></div>
      <ul class="service__list">
        <li>Sensory Processing Disorder</li>
        <li>Balance, Coordination, Strength, and Endurance</li>
        <li>Fine Motor and Handwriting</li>
        <li>Visual- Motor Integration</li>
        <li>Play and Social Skills</li>
        <li>Feeding and Oral Motor Skills</li>
        <li>Self-Care</li>
        <li>Academic and Cognitive Skills</li>
        <li>Behavioral Difficulties</li>
        <li>Developmental Delays</li>
      </ul>
    </div>
    <svg class="swoosh" style="left:0;bottom:0" width="380" height="130" viewBox="0 0 380 130" aria-hidden="true">
      <path d="M0 0 C60 70 180 110 380 96 L380 130 L0 130 Z" fill="var(--lime)"/>
    </svg>
    <div class="photo-pair">
      <div class="photo photo--small photo--bowl" role="img" aria-label="Toddler laughing with a bowl of spaghetti on his head"></div>
      <div class="photo photo--small photo--ball" role="img" aria-label="Young child playing on a large blue therapy ball"></div>
    </div>
  </section>

  <section class="panel panel--speech">
    <div class="service">
      <h2 class="service__title">Speech Therapy</h2>
      <p class="service__lead">Helping children speak, communicate and understand language.</p>
      <div class="service__rule"></div>
      <ul class="service__list">
        <li>Expressive and Receptive Language</li>
        <li>Speech and Language Developmental Milestones</li>
        <li>Articulation / Intelligibility</li>
        <li>Speech Fluency</li>
        <li>Pragmatics and Social Skills</li>
        <li>Literacy and Vocabulary</li>
        <li>Apraxia of Speech</li>
        <li>Augmentative and Alternative Communication</li>
        <li>Feeding and Oral Motor</li>
      </ul>
    </div>
    <div class="service">
      <h2 class="service__title">Sensory Integration</h2>
      <p class="service__lead">Gradually increasing play based activities to improve a child's nervous system. Helping children learn to self-regulate their emotions, behaviors and arousal levels.</p>
      <div class="service__rule"></div>
      <ul class="service__list">
        <li>Autism and ADHD</li>
        <li>Sensory Processing Disorder</li>
        <li>Poor Tolerance of Sensory Stimuli from the Environment</li>
        <li>Meltdowns and Tantrums</li>
        <li>Poor Balance/Body Awareness</li>
        <li>Poor Attention and Concentration</li>
        <li>Poor Self-Regulation</li>
        <li>Behavior and Social Difficulties</li>
        <li>Poor Motor Coordination and Motor Planning</li>
        <li>Aggression, Frustration or Avoidance Behaviors</li>
      </ul>
    </div>
    <div class="brand">
      <span class="brand__mark"></span>
      <span class="brand__name">Brightbrook Pediatric Therapy</span>
    </div>
  </section>

  <section class="panel panel--feeding">
    <svg class="swoosh" style="right:0;top:0" width="380" height="120" viewBox="0 0 380 120" aria-hidden="true">
      <path d="M80 0 L380 0 L380 70 C300 20 190 8 80 0 Z" fill="var(--lime)"/>
    </svg>
    <div class="service" style="position:relative;margin-top:18px">
      <h2 class="service__title">Feeding Therapy</h2>
      <p class="service__lead">Providing skilled assessment and intervention to children with feeding difficulties.</p>
      <div class="service__rule"></div>
      <ul class="service__list">
        <li>Food Aversions</li>
        <li>Food Refusal</li>
        <li>Very Picky Eating</li>
        <li>Avoidance of Certain Textures</li>
        <li>Gagging and Vomiting</li>
        <li>Oral Motor/ Chewing Difficulties</li>
        <li>Limited Diet/Food Repertoire</li>
      </ul>
    </div>
    <div class="service">
      <h2 class="service__title">Physical Therapy</h2>
      <p class="service__lead">Helping children move and interact within their environment smoothly and confidently.</p>
      <div class="service__rule"></div>
      <ul class="service__list">
        <li>Torticollis</li>
        <li>Walking and Mobility</li>
        <li>Developmental Motor Milestones</li>
        <li>Balance, Coordination, Motor Planning</li>
        <li>Strength, Muscle Tone and Range of Motion</li>
        <li>Sports Injuries</li>
        <li>Toe Walking</li>
        <li>Myofascial Release</li>
        <li>Postural Control and Positioning</li>
      </ul>
    </div>
    <div class="service">
      <h2 class="service__title">Group Therapy</h2>
      <p class="service__lead">Using peer role models to learn new and challenging skills.</p>
      <div class="service__rule"></div>
      <ul class="service__list">
        <li>Social Groups</li>
        <li>Feeding Groups</li>
      </ul>
    </div>
    <svg class="swoosh" style="right:0;bottom:0" width="380" height="80" viewBox="0 0 380 80" aria-hidden="true">
      <path d="M0 80 L0 40 C120 44 260 30 380 0 L380 80 Z" fill="var(--lime)"/>
    </svg>
    <p class="note">**More Group Classes Coming Soon</p>
  </section>

</main>
</body>
</html>
```